20 year old business card needs re-design

We need to redesign our corporate business card look. We need something that appears more modern, eye catchy but professional.

Target Market(s)

manufacturing industry

Industry/Entity Type

Manufacturer

Contact Information for Business Card

One side can have the logo. Other side can have contact information.

Font styles to use
Serif

Colors
3277b5
33b8a4
ffffff

Requirements
Must have
• Eye catchy - need to standout from the crowd. company logo cannot change. Full name, job title, phone number and email address.
Should not have
• Fax, business address is not necessary.

```html
<!DOCTYPE html>
<html lang="en">
<head>
<meta charset="utf-8">
<title>Norvek Industrial – Business Card</title>
<link rel="stylesheet" href="https://fonts.googleapis.com/css2?family=Lato:wght@300;400;700;900&display=swap">
<style>
  :root {
    --stage: #2b2b2b;
    --front-blue: #b4c3e2;
    --front-blue-light: #c9d4ec;
    --back-white: #f4f4f4;
    --back-grey: #e4e4e4;
    --brand-blue: #3277b5;
    --name-blue: #3a7dc9;
    --ink: #1c1c1c;
    --band-black: #161616;
    --white: #ffffff;
  }
  * { box-sizing: border-box; margin: 0; padding: 0; }
  html, body { width: 1200px; height: 1031px; overflow: hidden; }
  body {
    background: var(--stage);
    font-family: "Lato", Arial, sans-serif;
    position: relative;
  }
  .card {
    position: absolute;
    left: 290px;
    width: 620px;
    height: 354px;
    border-radius: 22px;
    overflow: hidden;
    box-shadow: 0 10px 30px rgba(0,0,0,.5);
  }
  .card-front { top: 131px; }
  .card-back { top: 546px; }

  .drawing-fill {
    position: absolute; inset: 0;
  }
  .card-front .drawing-fill {
    background: radial-gradient(ellipse at 50% 45%, var(--front-blue-light), var(--front-blue) 75%);
  }
  .card-back .drawing-fill {
    background: radial-gradient(ellipse at 55% 45%, var(--white), var(--back-grey) 85%);
  }

  .brand-mark {
    position: absolute; left: 0; right: 0; top: 150px;
    text-align: center;
    font-weight: 900;
    font-size: 50px;
    letter-spacing: 1px;
    color: var(--ink);
  }
  .brand-mark .brand-dot {
    display: inline-block; width: 22px; height: 22px;
    background: var(--brand-blue); border-radius: 50%;
    margin-right: 14px; vertical-align: 4px;
  }

  .identity { position: absolute; left: 120px; top: 42px; }
  .person-name {
    font-weight: 900; font-size: 40px; color: var(--name-blue);
    margin-left: 148px; line-height: 1;
  }
  .job-row { display: flex; align-items: flex-end; margin-top: 4px; }
  .job-rule { width: 140px; height: 1px; background: var(--ink); margin-right: 8px; margin-bottom: 8px; }
  .job-title { font-weight: 300; font-size: 30px; color: var(--ink); line-height: 1.1; }

  .locations-band {
    position: absolute; left: 0; right: 0; top: 158px; height: 34px;
    display: flex; font-size: 19px; color: var(--white);
  }
  .locations-label {
    background: var(--brand-blue); width: 180px;
    display: flex; align-items: center; justify-content: flex-end; padding-right: 10px;
  }
  .locations-list {
    background: var(--band-black); flex: 1;
    display: flex; align-items: center; padding-left: 10px; font-weight: 700;
  }

  .contact-list { position: absolute; left: 280px; top: 218px; list-style: none; }
  .contact-list li {
    display: flex; align-items: center; gap: 8px;
    font-size: 17px; color: var(--ink); line-height: 25px;
  }
  .contact-list svg { width: 14px; height: 14px; flex: none; }
  .contact-web strong { font-weight: 900; }
</style>
</head>
<body>
  <section class="card card-front">
    <div class="drawing-fill" role="img" aria-label="Faint white engineering blueprint linework with gears over pale blue"></div>
    <div class="brand-mark"><span class="brand-dot"></span>Norvek Industrial</div>
  </section>

  <section class="card card-back">
    <div class="drawing-fill" role="img" aria-label="Faint grey engineering blueprint linework with gears over white"></div>
    <div class="identity">
      <div class="person-name">Sam Reline</div>
      <div class="job-row"><span class="job-rule"></span><span class="job-title">Senior Project Manager</span></div>
    </div>
    <div class="locations-band">
      <div class="locations-label">Global Locations:</div>
      <div class="locations-list">USA, Mexico, China, Taiwan, South Korea, Japan</div>
    </div>
    <ul class="contact-list">
      <li class="contact-phone">
        <svg viewBox="0 0 14 14"><circle cx="7" cy="7" r="7" fill="#3277b5"/><path d="M4.5 3.8l1.4 1.6-.7 1c.5 1 1.3 1.8 2.3 2.3l1-.7 1.6 1.4-.9 1.1C6.6 10.3 3.7 7.4 3.5 4.7z" fill="#fff"/></svg>
        555-014-2200 xt 104
      </li>
      <li class="contact-email">
        <svg viewBox="0 0 14 14"><rect x="1" y="3" width="12" height="8" fill="#3277b5"/><path d="M1 3l6 5 6-5" stroke="#fff" fill="none"/></svg>
        sam@norvekindustrial.com
      </li>
      <li class="contact-web">
        <svg viewBox="0 0 14 14"><circle cx="7" cy="7" r="6.5" fill="#3277b5"/><path d="M1 7h12M7 1c-3 3-3 9 0 12M7 1c3 3 3 9 0 12" stroke="#fff" fill="none" stroke-width=".9"/></svg>
        <span><strong>NorvekIndustrial</strong>.com</span>
      </li>
    </ul>
  </section>
</body>
</html>
```